Non fiction leadership Book Cover design needed for “Stay Bold: Build On Lasting Discipline”

I need a front cover design for a new book 6 X 9 traditional non-fiction book.

Title: "Stay BOLD - Build On Lasting Discipline"

The subtitle is not finalized- so use 2 lines of smaller dummy text

My brand guide is attached (please use the tan color sparingly)

I'd like to see BOLD look like it is in motion and "flying" across the page

Need CREATIVE designs and options

Do not want my picture on the front cover - I do want it on the back cover.

On the front cover I’d like to see creative use of font to create movement on “BOLD”

Target Market(s)

Business leaders

Industry/Entity Type

Aviation

Font styles to use
Other font styles liked:
• See style guide- can add additional font (modern script or san serif)

Colors
0054AA
0677BA
7BADD7
CADEEF
E8F1F8
EB3D1F
EC4F4E
F09395
F8D3D4
FCEDEE

Requirements
Must have
• Creative font use, using perspective to create movement/motion on BOLD
Should not have
• My picture on the front cover- my picture should be on the back cover

```html
<!DOCTYPE html>
<html lang="en">
<head>
<meta charset="utf-8">
<title>Stay Bold: Build On Lasting Discipline — Book Cover</title>
<link rel="stylesheet" href="https://fonts.googleapis.com/css2?family=Bebas+Neue&family=Great+Vibes&family=Montserrat:wght@600&display=swap">
<style>
  :root {
    --page-bg: #eeeeee;
    --navy-deep: #041a45;
    --navy-mid: #132f6b;
    --navy-light: #1f468f;
    --white: #ffffff;
    --gold-light: #fff3dc;
    --gold: #ffd276;
    --gold-deep: #f2b94a;
  }
  * { margin: 0; padding: 0; box-sizing: border-box; }
  html, body {
    width: 883px;
    height: 1200px;
    overflow: hidden;
    background: var(--page-bg);
  }
  .cover {
    position: absolute;
    left: 77px;
    top: 58px;
    width: 730px;
    height: 1094px;
    overflow: hidden;
    background:
      radial-gradient(ellipse 420px 360px at 78% 28%, var(--navy-light) 0%, rgba(31,70,143,0) 100%),
      linear-gradient(100deg, var(--navy-deep) 0%, var(--navy-mid) 55%, #1b3a7a 100%);
  }
  .subtitle {
    position: absolute;
    top: 68px;
    left: 0;
    width: 100%;
    text-align: center;
    color: var(--white);
    font-family: "Montserrat", sans-serif;
    font-weight: 600;
    font-size: 21.5px;
    line-height: 27px;
    letter-spacing: 0.4px;
  }
  .jet-photo {
    position: absolute;
    left: 0;
    top: 0;
    width: 730px;
    height: 600px;
    z-index: 0;
  }
  .title { position: absolute; inset: 0; z-index: 1; font-weight: normal; }
  .title-lead {
    position: absolute;
    top: 170px;
    left: 253px;
    color: var(--white);
    font-family: "Bebas Neue", sans-serif;
    font-size: 148px;
    line-height: 1;
    letter-spacing: 1px;
  }
  .title-script {
    position: absolute;
    top: 350px;
    left: 0;
    width: 730px;
    text-align: center;
    font-family: "Great Vibes", cursive;
    font-size: 255px;
    line-height: 1.1;
    background: linear-gradient(180deg, var(--gold-light) 0%, var(--gold) 60%, var(--gold-deep) 100%);
    -webkit-background-clip: text;
    background-clip: text;
    color: transparent;
    transform: rotate(-6deg);
  }
  .title-expansion {
    position: absolute;
    top: 688px;
    left: 0;
    width: 684px;
    text-align: center;
    color: var(--white);
    font-family: "Bebas Neue", sans-serif;
    font-size: 66px;
    line-height: 0.95;
    padding-left: 16px;
  }
  .author {
    position: absolute;
    top: 985px;
    left: 0;
    width: 730px;
    text-align: center;
    font-family: "Bebas Neue", sans-serif;
    font-size: 74px;
    line-height: 1;
    letter-spacing: 1px;
    background: linear-gradient(180deg, var(--gold-light) 0%, var(--gold) 55%, var(--gold-deep) 100%);
    -webkit-background-clip: text;
    background-clip: text;
    color: transparent;
  }
</style>
</head>
<body>
  <main class="cover">
    <p class="subtitle">LOREM IPSUM DOLOR SIT AMET, CONSECTETUR<br>ADIPISCING ELIT, SED DO EIUSMOD TEMPOR.</p>
    <svg class="jet-photo" viewBox="0 0 730 600" role="img" aria-label="Photo of a white jet airliner climbing across a blue sky, trailing a long contrail">
      <defs>
        <linearGradient id="contrail" x1="0" y1="1" x2="1" y2="0">
          <stop offset="0" stop-color="#dfe9f8" stop-opacity="0"/>
          <stop offset="0.6" stop-color="#dfe9f8" stop-opacity="0.25"/>
          <stop offset="1" stop-color="#ffffff" stop-opacity="0.55"/>
        </linearGradient>
      </defs>
      <polygon points="40,460 560,245 580,262 60,480" fill="url(#contrail)"/>
      <ellipse cx="600" cy="235" rx="55" ry="22" fill="#ffffff" fill-opacity="0.35" transform="rotate(-20 600 235)"/>
    </svg>
    <h1 class="title">
      <span class="title-lead">STAY</span>
      <span class="title-script">Bold</span>
      <span class="title-expansion">BUILD ON LASTING<br>DISCIPLINE</span>
    </h1>
    <p class="author">MARGARET HOLLOWAY</p>
  </main>
</body>
</html>
```